Website Banner Redesign for Kelvra Cargo Depot

Business Name:
KELVRA CARGO DEPOT

About Us:
- We’re a proudly Australian company that designs and builds tough, reliable toolboxes for Utes, Trucks, and Campervans. Our products are made to handle harsh conditions and are trusted by tradies, off-roaders, and professional fleets across the country.

Project Goal:
- We want to refresh our homepage and category banners with bold, modern designs that better showcase our products and value proposition.

Why We’re Updating:
Our current banners show the products well, but we want to improve:
Visual impact and hierarchy
- Readability of text (especially on mobile)
- Clearer calls-to-action (CTAs)
- Brand messaging around “Built Tough”, “Aussie Made”, and “Custom Fit-Outs”

Target Audience:
- Tradespeople
- 4x4 & off-road enthusiasts
- Caravan & camping community
- Ute/Truck/Caravan dealerships
- Fleet and commercial buyers

Design Style We Want:
- Bold, confident, rugged
- Clean layout with clear focal points
- Strong product imagery (we’ll supply photos)
- Use of brand colors: Black, White, Red, Grey
- Professional, not too busy or cluttered

Banner Uses:
- Homepage hero banner
- Category landing pages

UTE TOOLBOXES - https://www.kelvracargo.com.au/aluminium-toolboxes/
Truck Boxes - https://www.kelvracargo.com.au/truck-toolboxes/
Canopies - https://www.kelvracargo.com.au/canopy/
Dog Boxes - https://www.kelvracargo.com.au/dog-boxes/
CAMPER BOXES - https://www.kelvracargo.com.au/camper-toolboxes/
Accessories - https://www.kelvracargo.com.au/accessories/

- Can be reused for desktop and mobile

Inspiration Style:
Think: 4x4 accessory brands, tough tradie gear, or clean eCommerce landing banners from premium auto suppliers.

Target Market(s)

All in Brief Above

Industry/Entity Type

Retail

Requirements
Must have
• A banner using our products only. A banner for each category, and 2 alternate banners for the home page.
Nice to have
• I have added some designs which i like..... Please take a look and take inspiration from them.

```html
<!DOCTYPE html>
<html lang="en">
<head>
<meta charset="utf-8">
<title>Accessible Gullwing Toolboxes – Kelvra Cargo Depot</title>
<link rel="stylesheet" href="https://fonts.googleapis.com/css2?family=Anton&display=swap">
<style>
  :root {
    --bg-dark: #1f272c;
    --bg-mid: #3a464d;
    --bg-light: #56636a;
    --headline: #ffffff;
    --tagline: #ffd200;
    --cta: #a81d4b;
    --cta-text: #ffffff;
    --placeholder-light: #c9cfd2;
    --placeholder-dark: #8f989d;
  }
  * { margin: 0; padding: 0; box-sizing: border-box; }
  html, body { width: 900px; height: 1200px; overflow: hidden; }
  body { font-family: "Anton", "Impact", sans-serif; background: var(--bg-dark); }
  .banner {
    position: relative;
    width: 900px;
    height: 1200px;
    overflow: hidden;
    background:
      radial-gradient(ellipse 420px 330px at 440px 650px, rgba(255,255,255,0.22), transparent 70%),
      radial-gradient(ellipse 700px 500px at 500px 350px, var(--bg-light), transparent 75%),
      linear-gradient(160deg, var(--bg-mid) 0%, var(--bg-dark) 70%, #161c20 100%);
  }
  .headline {
    position: absolute;
    left: 64px;
    top: 58px;
    color: var(--headline);
    font-size: 140px;
    line-height: 144px;
    font-weight: 400;
    text-transform: uppercase;
    letter-spacing: 1px;
  }
  .product-image {
    position: absolute;
    left: 80px;
    top: 507px;
    width: 740px;
    height: 295px;
    border-radius: 8px;
    background: radial-gradient(ellipse at 50% 45%, var(--placeholder-light) 0%, var(--placeholder-dark) 100%);
  }
  .tagline {
    position: absolute;
    left: 70px;
    top: 821px;
    color: var(--tagline);
    font-size: 73px;
    line-height: 81px;
    font-weight: 400;
    text-transform: uppercase;
  }
  .cta {
    position: absolute;
    left: 65px;
    top: 1014px;
    width: 440px;
    height: 125px;
    border-radius: 18px;
    background: var(--cta);
    color: var(--cta-text);
    font-size: 80px;
    line-height: 125px;
    text-align: center;
    text-transform: uppercase;
    text-decoration: none;
  }
</style>
</head>
<body>
  <main class="banner">
    <h1 class="headline">Accessible<br>Gullwing<br>Toolboxes</h1>
    <div class="product-image" role="img" aria-label="Product photo: checker-plate aluminium gullwing toolbox with both lids raised"></div>
    <p class="tagline">Easy access to your<br>tools from both side</p>
    <a class="cta" href="https://www.kelvracargo.com.au/aluminium-toolboxes/">View More</a>
  </main>
</body>
</html>
```